Brook Refrigeration. Refrigeration and air conditioning specialists.

We need a website to promote our business. We would a modern simple design using the colours from our logo and black. We want it to be fun but proffesional.

Target Market(s)

Commercial

Number of Pages Required

4 page

Requirements
Must have
• Home Page, About Us, Services and Contact Us.
• 24/7 365 days service available.
• Brook Refrigeration's dedicated team specialises in commercial refrigeration and air conditioning equipment.
• Based in Joondalup, we cover Perth Metro and surrounding areas.
Nice to have
• KNOWLEDGE . EXPERIENCE . PASSION in bold.
• Our experienced and highly trained technicians provide extensive knowledge and exceptional skills for your commercial refrigeration and air conditioning requirements.
• Pictures of commercial refrigeration.
Should not have
• No mention of domestic services.

```html
<!DOCTYPE html>
<html lang="en">
<head>
<meta charset="utf-8">
<title>About Us – Brook Refrigeration</title>
<link href="https://fonts.googleapis.com/css2?family=Lato:wght@400;700;900&display=swap" rel="stylesheet">
<style>
:root{
  --green:#93f05b;
  --purple:#2d1b4e;
  --ink:#2a2a2a;
  --text:#4a4a4a;
  --muted:#6a6a6a;
  --rule:#e2e2e2;
  --white:#ffffff;
}
*{box-sizing:border-box;margin:0;padding:0}
html,body{width:699px;height:1200px;overflow:hidden;background:var(--white)}
body{position:relative;font-family:'Lato',sans-serif;color:var(--text)}
.abs{position:absolute}

/* header */
.brand{left:44px;top:20px;font-weight:900;font-size:16px;color:var(--green);letter-spacing:.2px}
.brand-footer{left:44px;top:1084px}
.follow{left:436px;top:13px;display:flex;align-items:center;gap:7px;font-size:8.5px;font-weight:700;color:var(--purple)}
.social-dot{width:10px;height:10px;border-radius:50%;background:var(--purple);display:inline-block}
.phone{left:553px;top:10px;display:flex;align-items:center;gap:7px;font-size:14px;font-weight:700;color:var(--purple)}
.nav{left:426px;top:38px;display:flex;font-size:9px;font-weight:700;color:var(--ink)}
.nav a{display:block;padding:0 10px;height:22px;line-height:22px;text-decoration:none;color:inherit}
.nav a+a{margin-left:6px}
.nav .active{background:var(--green)}

/* hero */
.hero{left:0;top:68px;width:699px;height:113px;background:linear-gradient(100deg,#7fdc4d 0%,#5fae3c 28%,#4a5a3e 48%,#3a3838 62%,#2f2844 82%,#3f2a6e 100%);display:flex;align-items:center;justify-content:center}
.hero h1{color:var(--white);font-size:16px;font-weight:700;letter-spacing:.3px}

/* intro */
.intro-text{left:44px;top:211px;width:350px;font-size:8.8px;line-height:16px;color:var(--text)}
.intro-photo{left:410px;top:216px;width:246px;height:167px;background:linear-gradient(160deg,#f2f2f2 0%,#d7d9dc 45%,#b9bcbf 75%,#cdb36a 100%)}
.btn{background:var(--green);color:var(--ink);font-weight:700;font-size:8.5px;text-align:center;font-family:inherit}
.read-more{left:44px;top:357px;width:88px;height:26px;line-height:26px}
.rule{left:44px;top:415px;width:612px;height:1px;background:var(--rule)}

/* offer */
.section-title{left:0;width:699px;text-align:center;font-size:16px;font-weight:900}
.offer-title{top:446px;color:var(--purple)}
.offer{top:496px;width:200px;text-align:center}
.offer .icon{width:58px;height:58px;border-radius:50%;background:var(--green);margin:0 auto 14px;display:flex;align-items:center;justify-content:center}
.offer h3{font-size:11.2px;line-height:14.5px;font-weight:700;color:var(--ink);margin-bottom:3px}
.offer p{width:170px;margin:0 auto;font-size:8.8px;line-height:13.6px;color:var(--muted)}

/* contact */
.contact-band{left:0;top:686px}
.contact-title{top:753px;color:var(--white)}
.field{background:var(--white);font-size:8.8px;color:#555;padding:0 9px;display:flex;align-items:center}
.field.area{align-items:flex-start;padding-top:10px}
.submit{left:305px;top:971px;width:88px;height:26px;line-height:26px}

/* footer */
.copyright{left:44px;top:1130px;font-size:7.3px;line-height:14px;color:var(--muted)}
.foot-col h4{font-size:8.5px;font-weight:700;color:var(--purple);margin-bottom:9px}
.foot-col li{list-style:none;font-size:8px;line-height:19px;color:var(--ink)}
.contact-list li{display:flex;align-items:center;gap:12px;line-height:16px}
.contact-list svg{width:7px;height:7px;flex:none}
.foot-social{display:flex;gap:10px;margin-top:4px}
.foot-social .social-dot{width:11px;height:11px}
</style>
</head>
<body>

<header>
  <div class="abs brand">Brook Refrigeration</div>
  <div class="abs follow">FOLLOW US <span class="social-dot" aria-label="Social profile link"></span><span class="social-dot" aria-label="Social profile link"></span></div>
  <div class="abs phone">
    <svg width="11" height="11" viewBox="0 0 24 24" aria-hidden="true"><path fill="#2d1b4e" d="M6.6 10.8a15 15 0 0 0 6.6 6.6l2.2-2.2c.3-.3.7-.4 1-.2 1.1.4 2.3.6 3.6.6.6 0 1 .4 1 1V20c0 .6-.4 1-1 1A17 17 0 0 1 3 4c0-.6.4-1 1-1h3.5c.6 0 1 .4 1 1 0 1.3.2 2.5.6 3.6.1.3 0 .7-.2 1z"/></svg>
    1300-555-018
  </div>
  <nav class="abs nav">
    <a href="#">HOME</a><a href="#" class="active">ABOUT</a><a href="#">SERVICES</a><a href="#">CONTACT</a>
  </nav>
</header>

<section class="abs hero"><h1>ABOUT US</h1></section>

<section>
  <p class="abs intro-text">Lorem ipsum dolor sit amet, consectetur adipiscing elit. Integer molestie odio sed nulla hendrerit, ac tincidunt purus bibendum. Mauris bibendum tortor nisi, non mattis lorem fringilla eget. Nam ac dictum neque, fringilla rutrum risus. Morbi sagittis mattis ex eget elementum. Nulla fringilla et sem eu dictum. Etiam faucibus facilisis ipsum, vel interdum leo posuere sed. Donec sagittis in eros ut volutpat. Fusce a condimentum nulla, ut dignissim mi. Praesent varius justo est, non volutpat lectus mollis at.<br>Donec at dolor nisi. Morbi eget lectus augue. Sed porttitor efficitur sem, in semper mauris porttitor vulputate.</p>
  <div class="abs intro-photo" role="img" aria-label="Photo of an empty commercial cold room with steel shelving"></div>
  <div class="abs btn read-more">READ MORE</div>
  <div class="abs rule"></div>
</section>

<section>
  <h2 class="abs section-title offer-title">WHAT WE OFFER</h2>
  <div class="abs offer" style="left:40px">
    <div class="icon">
      <svg width="28" height="28" viewBox="0 0 28 28" aria-hidden="true"><circle cx="14" cy="14" r="11" fill="none" stroke="#2d1b4e" stroke-width="3"/><path d="M14 8v6h-5" fill="none" stroke="#2d1b4e" stroke-width="2.6" stroke-linecap="round"/></svg>
    </div>
    <h3>24/7 365 DAYS SERVICE<br>AVAILABLE</h3>
    <p>Lorem ipsum dolor sit amet, consectetur adipiscing elit. In ut leo sit amet mauris pellentesque lobortis</p>
  </div>
  <div class="abs offer" style="left:249px">
    <div class="icon" role="img" aria-label="Technician icon"></div>
    <h3>EXPERIENCED &amp; HIGHLY TRAINED<br>TECHNICIANS</h3>
    <p>Lorem ipsum dolor sit amet, consectetur adipiscing elit. In ut leo sit amet mauris pellentesque lobortis</p>
  </div>
  <div class="abs offer" style="left:460px">
    <div class="icon">
      <svg width="22" height="28" viewBox="0 0 22 28" aria-hidden="true"><path fill="#2d1b4e" d="M11 1a9 9 0 0 0-9 9c0 7 9 17 9 17s9-10 9-17a9 9 0 0 0-9-9zm0 12.5A3.5 3.5 0 1 1 11 6.5a3.5 3.5 0 0 1 0 7z"/></svg>
    </div>
    <h3>SERVICE BASED IN<br>JOONDALUP</h3>
    <p>Lorem ipsum dolor sit amet, consectetur adipiscing elit. In ut leo sit amet mauris pellentesque lobortis</p>
  </div>
</section>

<section>
  <svg class="abs contact-band" width="699" height="380" viewBox="0 0 699 380" role="img" aria-label="Photo of a supermarket aisle with refrigerated display cases">
    <defs>
      <linearGradient id="storeTone" x1="0" y1="0" x2="1" y2="1">
        <stop offset="0" stop-color="#5a5e62"/>
        <stop offset=".5" stop-color="#44484c"/>
        <stop offset="1" stop-color="#5f6468"/>
      </linearGradient>
    </defs>
    <polygon points="0,42 699,0 699,344 0,378" fill="url(#storeTone)"/>
  </svg>
  <h2 class="abs section-title contact-title">QUICK CONTACT</h2>
  <div class="abs field" style="left:132px;top:795px;width:210px;height:29px">Name</div>
  <div class="abs field" style="left:357px;top:795px;width:210px;height:29px">Phone Name</div>
  <div class="abs field" style="left:132px;top:835px;width:210px;height:29px">Email Address</div>
  <div class="abs field" style="left:357px;top:835px;width:210px;height:29px">Company Name</div>
  <div class="abs field area" style="left:132px;top:873px;width:435px;height:79px">Message</div>
  <div class="abs btn submit">SUBMIT</div>
</section>

<footer>
  <div class="abs brand brand-footer">Brook Refrigeration</div>
  <p class="abs copyright">Copyright © 2018 Brook Refrigeration Pty Ltd.<br>All Rights Reserved.<br>ABN 00 000 000 000.</p>
  <div class="abs foot-col" style="left:241px;top:1076px">
    <h4>SITE MAP</h4>
    <ul><li>Home</li><li>About</li><li>Services</li><li>Contact Us</li></ul>
  </div>
  <div class="abs foot-col" style="left:365px;top:1076px">
    <h4>CONTACT US</h4>
    <ul class="contact-list">
      <li style="line-height:12.5px">12 Harbour Lane<br>Joondalup WA 6027</li>
      <li><svg viewBox="0 0 24 24" aria-hidden="true"><path fill="#2a2a2a" d="M6.6 10.8a15 15 0 0 0 6.6 6.6l2.2-2.2c.3-.3.7-.4 1-.2 1.1.4 2.3.6 3.6.6.6 0 1 .4 1 1V20c0 .6-.4 1-1 1A17 17 0 0 1 3 4c0-.6.4-1 1-1h3.5c.6 0 1 .4 1 1 0 1.3.2 2.5.6 3.6.1.3 0 .7-.2 1z"/></svg>1-800-555-0142</li>
      <li><svg viewBox="0 0 24 24" aria-hidden="true"><path fill="#2a2a2a" d="M2 5h20v14H2z"/><path d="M2 5l10 8 10-8" fill="none" stroke="#fff" stroke-width="2"/></svg>hello@brookrefrig.example</li>
      <li><svg viewBox="0 0 22 28" aria-hidden="true"><path fill="#2a2a2a" d="M11 1a9 9 0 0 0-9 9c0 7 9 17 9 17s9-10 9-17a9 9 0 0 0-9-9zm0 12.5A3.5 3.5 0 1 1 11 6.5a3.5 3.5 0 0 1 0 7z"/></svg>Map Direction</li>
    </ul>
  </div>
  <div class="abs foot-col" style="left:528px;top:1076px">
    <h4>FOLLOW US</h4>
    <div class="foot-social"><span class="social-dot" aria-label="Social profile link"></span><span class="social-dot" aria-label="Social profile link"></span></div>
  </div>
</footer>

</body>
</html>
```